Business card design for holistic health care clinic

We need a double-sided business card design for our holistic health care clinic that integrates our logo design and also its color scheme. My business is called Valmira. It is an integrative medicine clinic. You have already done the logo for me. Please ensure an elegant and upscale design that is not cluttered, but still has all the necessary information (please see below for details).

Target Market(s)

Wellness, fitness, rehabilitation for educated, well-traveled open-minded clients who are focused on natural, organic, balanced and preventive healthcare and lifestyle.

Industry/Entity Type

Medical

Contact Information for Business Card

Modern, clean.

Number of Pages Required

1 page

Font styles to use
Serif
Sans Serif

Colors

Designer to choose colors to be used in the design.

Requirements
Must have
• Logo on one side, all other information on the other side.
• Other information should include:
• Tobias Wrenfeld - DOE, CPT, LMT
• 4100 East Marrow Drive
• Austin, TX 78119
• 512 555 0148
• 818 555 0192
• info@ValmiraHealth.example
• t.wrenfeld@ValmiraHealth.example
Nice to have
• Darker background on front - but not totally black - shaded/dark gray.

```html
<!DOCTYPE html>
<html lang="en">
<head>
<meta charset="utf-8">
<title>Valmira Business Card</title>
<link rel="stylesheet" href="https://fonts.googleapis.com/css2?family=PT+Sans:wght@400;700&display=swap">
<style>
  :root {
    --backdrop: #e4e4e4;
    --card: #2b2b2c;
    --accent: #1a8fcf;
    --text: #ececec;
    --shadow: rgba(0,0,0,0.35);
  }
  * { margin: 0; padding: 0; box-sizing: border-box; }
  html, body {
    width: 1200px; height: 808px; overflow: hidden;
    background: var(--backdrop);
    font-family: "PT Sans", sans-serif;
  }
  .stage { position: relative; width: 1200px; height: 808px; }
  .card {
    position: absolute; top: 260px;
    width: 505px; height: 289px;
    background: var(--card);
    box-shadow: 1px 2px 4px var(--shadow);
    overflow: hidden;
  }
  .card--info { left: 94px; }
  .card--brand { left: 609px; }

  .person { position: absolute; left: 25px; top: 119px; }
  .person__name {
    color: var(--accent); font-weight: 700; font-size: 17px;
    letter-spacing: 0.2px; text-transform: uppercase; line-height: 1;
  }
  .person__credentials {
    color: var(--accent); font-weight: 700; font-size: 9px;
    margin-top: 3px; line-height: 1;
  }
  .address {
    position: absolute; left: 25px; top: 163px;
    color: var(--text); font-size: 13px; line-height: 16px;
  }
  .contacts {
    position: absolute; left: 25px; top: 203px;
    list-style: none; color: var(--text); font-size: 13px;
  }
  .contacts li { display: flex; align-items: center; height: 16px; }
  .contacts svg { width: 12px; height: 12px; margin-right: 7px; fill: var(--accent); flex: none; }

  .brand { position: absolute; left: 0; right: 37px; top: 190px; text-align: right; }
  .brand__name {
    color: var(--accent); font-weight: 700; font-size: 40px;
    line-height: 1; text-transform: uppercase; letter-spacing: 0.5px;
  }
  .brand__descriptor {
    color: var(--accent); font-weight: 700; font-size: 11.5px;
    margin-top: 2px; line-height: 1;
  }
  .brand__tagline {
    color: #fff; font-weight: 700; font-size: 13px;
    margin-top: 3px; line-height: 1;
  }
</style>
</head>
<body>
<main class="stage">
  <section class="card card--info" aria-label="Card back with contact details">
    <div class="person">
      <h1 class="person__name">Tobias Wrenfeld</h1>
      <p class="person__credentials">DOE, CPT, LMT</p>
    </div>
    <address class="address">4100 East Marrow Drive<br>Austin, TX 78119</address>
    <ul class="contacts">
      <li><svg viewBox="0 0 12 12" aria-hidden="true"><path d="M1 4c0-2 2-3 5-3s5 1 5 3l-2 1-1-1.5H4L3 5 1 4zM3 6h6l1 5H2z"/></svg>512 555 0148</li>
      <li><svg viewBox="0 0 12 12" aria-hidden="true"><path d="M3 0h6v12H3zM4 1.5v7.5h4V1.5z"/></svg>818 555 0192</li>
      <li><svg viewBox="0 0 12 12" aria-hidden="true"><path d="M0 2.5h12v1L6 7 0 3.5zM0 5l6 3.5L12 5v4.5H0z"/></svg>t.wrenfeld@ValmiraHealth.example</li>
      <li><svg viewBox="0 0 12 12" aria-hidden="true"><circle cx="6" cy="6" r="5.5"/></svg>www.ValmiraHealth.example</li>
    </ul>
  </section>

  <section class="card card--brand" aria-label="Card front with brand name">
    <div class="brand">
      <p class="brand__name">Valmira</p>
      <p class="brand__descriptor">Integrative Holistic Medicine</p>
      <p class="brand__tagline">helping the body help itself</p>
    </div>
  </section>
</main>
</body>
</html>
```